Powerpoint design template for LUMOTEX for new digital platform

We would like to use a PowerPoint template, we would like to create a new page, we would like to create a new digital platform LUMOTEX for schools and parents for the creation of playful communication and educational tools for children to enhance their positive development, amaze them learn in a playful way. This platform is going to be the most creative, stimulating and innovative classroom, easy to use and fast to implement. Scrapbooking, collages ... Magazine, newsletters Diplomla / awards Slideshows Facebook Calendars Organizers Greetings Games ... This powerpoint template will be used essential to We are looking for a professional design, positioning our brand in the children market with an adult hearing. so you will need to find a good deal. Primary target: nurseries & schools from 0 to 18 years old and universities (in 2nd phase) Secondary target: small & medium businesses Third target: general public, and TPE If it is a color scheme, then it is suggested that it be marketed in Europe (UK, Italy, Spain) and in a 2nd Stage USA and other countries. multiple options for front page, insidious pages (multiple styles with limited text and extended text) and final contact page We need something to read, we can not do it too much, but we can not do it. , and inside pages aligned to our logo

Target Market(s)

Target 1; Education with teacher Target 2; parents and grandparents

Industry/Entity Type

Education

Font styles to use
Other font styles liked:
• not decided. but not too fancy

Requirements
Must have
• Multi page options for front page, page insides (multiple styles with limited text and extended text) and final page contact
Nice to have
• do not have a lot of ideas. We need something to read, we can not get away from it
Should not have
• not too fancy and busy: keep clarity & simplicity while reassuring on quality

```html
<!DOCTYPE html>
<html lang="en">
<head>
<meta charset="utf-8">
<title>LUMOTEX – Inside Page</title>
<link href="https://fonts.googleapis.com/css2?family=Oswald:wght@500&family=Roboto+Condensed:wght@400&display=swap" rel="stylesheet">
<style>
  :root {
    --lime: #d7e03e;
    --lime-deep: #b9c92a;
    --white: #ffffff;
    --pink: #e6488e;
    --orange: #f7941d;
    --ink: #2b2b22;
    --muted: #5d5d55;
    --photo-a: #ecd0b0;
    --photo-b: #cfa887;
  }
  * { margin: 0; padding: 0; box-sizing: border-box; }
  html, body { width: 1200px; height: 900px; overflow: hidden; background: var(--lime); }
  .slide {
    position: relative;
    width: 1200px;
    height: 900px;
    overflow: hidden;
    background: var(--lime);
    font-family: "Roboto Condensed", "Arial Narrow", sans-serif;
    color: var(--ink);
  }
  .slide__shapes { position: absolute; inset: 0; }
  .slide__photo {
    position: absolute;
    inset: 0;
    clip-path: polygon(876px 138px, 1200px 138px, 1200px 812px, 433px 812px);
    background: radial-gradient(circle at 45% 55%, #f2d25a 0%, #7fc4dc 22%, var(--photo-a) 45%, var(--photo-b) 100%);
  }
  .brand {
    position: absolute;
    top: 30px;
    left: 1000px;
    display: flex;
    flex-direction: column;
    gap: 6px;
  }
  .brand__row { display: flex; align-items: center; gap: 10px; }
  .brand__mark { width: 22px; height: 22px; background: var(--lime-deep); }
  .brand__name {
    font-family: "Oswald", "Arial Narrow", sans-serif;
    font-weight: 500;
    font-size: 36px;
    line-height: 1;
    color: var(--pink);
    letter-spacing: 1px;
  }
  .brand__tagline {
    font-size: 11px;
    line-height: 1.2;
    letter-spacing: 1.5px;
    color: var(--muted);
    text-transform: uppercase;
    padding-left: 2px;
  }
  .content { position: absolute; left: 48px; top: 144px; width: 660px; }
  .content__title {
    font-family: "Oswald", "Arial Narrow", sans-serif;
    font-weight: 500;
    font-size: 42px;
    line-height: 1.1;
    color: var(--pink);
    margin-bottom: 12px;
  }
  .content__body { font-size: 22px; line-height: 40.6px; }
  .footer__url {
    position: absolute;
    left: 21px;
    top: 844px;
    font-size: 24px;
    color: var(--ink);
  }
  .footer__page {
    position: absolute;
    right: 22px;
    top: 840px;
    font-size: 24px;
    color: var(--ink);
  }
</style>
</head>
<body>
<main class="slide">
  <svg class="slide__shapes" width="1200" height="900" viewBox="0 0 1200 900" aria-hidden="true">
    <polygon points="930,0 955,0 362,900 337,900" fill="var(--lime-deep)"/>
    <polygon points="955,0 972,0 379,900 362,900" fill="var(--white)"/>
    <polygon points="960,0 1200,0 1200,138 876,138" fill="var(--white)"/>
    <polygon points="1010,20 1170,20 1130,110 970,110" fill="var(--lime)" opacity="0.55"/>
    <polygon points="433,812 1200,812 1200,900 375,900" fill="var(--white)"/>
    <polygon points="429,818 1200,818 1200,900 379,900" fill="var(--orange)"/>
  </svg>

  <div class="slide__photo" role="img" aria-label="Photo of a smiling child holding up a hand painted in bright rainbow colours"></div>

  <div class="brand">
    <div class="brand__row">
      <span class="brand__mark"></span>
      <span class="brand__name">LUMOTEX</span>
    </div>
    <span class="brand__tagline">Your tagline<br>goes here</span>
  </div>

  <section class="content">
    <h1 class="content__title">SUBTEXT HERE</h1>
    <p class="content__body">
      Toffee caramels candy canes bonbon bonbon soufflé bonbon wafer.<br>
      Topping I love halvah I love. Jujubes lemon drops I love jelly pie<br>
      chocolate bar. Biscuit oat cake carrot cake. Muffin jelly beans<br>
      chocolate chocolate. Sugar plum I love cheesecake<br>
      marshmallow honey cake sweet cookies topping<br>
      jelly gummies. Toffee caramels candy canes bonbon<br>
      bonbon soufflé bonbon wafer. Topping I love halvah I love.<br>
      Jujubes lemon drops I love jelly pie chocolate bar.<br>
      Biscuit oat cake carrot cake. Muffin jelly beans<br>
      chocolate chocolate. Sugar plum I love cheesecake<br>
      marshmallow honey cake sweet cookies topping<br>
      jelly gummies.
    </p>
  </section>

  <footer>
    <span class="footer__url">www.lumotex.com</span>
    <span class="footer__page">Page : 01</span>
  </footer>
</main>
</body>
</html>
```